jewellery store flyer

Front to show
-company name and logo
underneath of company name, I want " The perfect creation" to be written.
-background bright tone jewellery or model wearing jewellery(prefer engagement and wedder or wedder set)

--------------------------------------------------------------
Back to show list of service and brief map of location
with addresss and contact detail

introducing newly established jewellery store with exclusive and unique jewellery. We offer you
-specialized in hand made jewellery
-on site jeweller and designer
-repair and restoring
-laser engraving and laser solder

5/41 Marrowind Crescent Griffith ACT 2603
02) 6174 3019
Enquiry: tansy.r@mailvane.com
---------------------------------------------------------------------
I have enclosed mockups that I made by myself, to show what I was thinking. this is just for reference. New flyer doesn't need to look the same.

I don't mind either holizontal nor vertical.
I don't mind if you add text or remove text that I have written above.
I want flyer to look morden and neat.

Good luck to you & me and enjoy creation.
Kind regards,
Petra

Target Market(s)

introducing newly established store.
aiming for engagement & wedding rings and remakes

Industry/Entity Type

It Company

Font styles to use
Other font styles liked:
• Monotype corsive for script but name and address for SERIF

Colors

Designer to choose colors to be used in the design.

Requirements
Must have
• background photo including jewellery
• company name and address
• service detail
Nice to have
• brief map of location( I have red circled few places that people know more on the map I attached here.)
• Map to be simplified please.
• Please do not use Google map directly.
• Opening hours: Mon-Fri 9.30 to 5.30 Sat 10.00 to 5

```html
<!DOCTYPE html>
<html lang="en">
<head>
<meta charset="utf-8">
<title>Marigold Jewellery – Flyer</title>
<link rel="stylesheet" href="https://fonts.googleapis.com/css2?family=Cinzel:wght@400;700&family=Lato:ital,wght@1,400&display=swap">
<style>
  :root {
    --page: #e4e4e6;
    --magenta: #c21a57;
    --magenta-deep: #7a1650;
    --plum: #4a1540;
    --gold: #c9a063;
    --gold-light: #e8c98c;
    --gold-text: #d9b46e;
    --silver: #f2f2f4;
    --silver-dark: #cfd0d4;
    --white: #ffffff;
    --berry: #b0164c;
    --ink-plum: #5a1a3c;
  }
  * { margin: 0; padding: 0; box-sizing: border-box; }
  html, body { width: 1200px; height: 1200px; overflow: hidden; background: var(--page); }
  .canvas { position: relative; width: 1200px; height: 1200px; }
  .flyer {
    position: absolute; left: 233px; width: 734px; height: 520px; overflow: hidden;
  }
  .flyer--front { top: 40px; }
  .flyer--back { top: 600px; }
  .flyer svg.art { position: absolute; inset: 0; width: 734px; height: 520px; }
  .txt { position: absolute; transform: translateX(-50%); white-space: nowrap; text-align: center; }

  /* front */
  .brand-mark { left: 554px; top: 24px; }
  .brand-mark .dot { width: 54px; height: 54px; border: 1.5px solid var(--white); border-radius: 50%; margin: 0 auto 8px; }
  .brand-mark .name { font-family: "Cinzel", serif; font-weight: 400; font-size: 17px; color: var(--white); letter-spacing: .5px; }
  .headline { left: 554px; top: 140px; font-family: "Cinzel", serif; font-weight: 700; color: var(--gold-text); font-size: 46px; line-height: 54px; }
  .tagline-lead { left: 554px; top: 318px; font-family: "Lato", sans-serif; font-style: italic; font-size: 31px; color: var(--white); }
  .tagline-main { left: 554px; top: 355px; font-family: "Cinzel", serif; font-size: 44px; color: var(--white); letter-spacing: 1px; }
  .call-label { left: 168px; top: 436px; font-family: "Cinzel", serif; font-size: 24px; color: var(--berry); letter-spacing: 1px; }
  .call-phone { left: 168px; top: 462px; font-family: "Cinzel", serif; font-weight: 700; font-size: 28px; color: var(--ink-plum); }

  /* back */
  .back-title { left: 513px; top: 36px; font-family: "Cinzel", serif; font-size: 38px; color: var(--white); }
  .service { left: 530px; font-family: "Lato", sans-serif; font-style: italic; font-size: 22px; color: var(--white); }
  .address { left: 536px; top: 484px; font-family: "Lato", sans-serif; font-style: italic; font-size: 13px; color: var(--white); }
</style>
</head>
<body>
<div class="canvas">

  <!-- Front -->
  <section class="flyer flyer--front">
    <svg class="art" viewBox="0 0 734 520" xmlns="http://www.w3.org/2000/svg">
      <defs>
        <linearGradient id="silverFront" x1="0" y1="0" x2="1" y2="1">
          <stop offset="0" stop-color="#d9dadd"/>
          <stop offset=".45" stop-color="#f7f7f8"/>
          <stop offset="1" stop-color="#cfd0d4"/>
        </linearGradient>
        <linearGradient id="magentaFront" x1="0" y1="0" x2="0" y2="1">
          <stop offset="0" stop-color="#b51d52"/>
          <stop offset=".5" stop-color="#c81c5c"/>
          <stop offset="1" stop-color="#5a1748"/>
        </linearGradient>
        <linearGradient id="goldBand" x1="0" y1="0" x2="1" y2="1">
          <stop offset="0" stop-color="#b88a4a"/>
          <stop offset=".5" stop-color="#ecd09a"/>
          <stop offset="1" stop-color="#b5844a"/>
        </linearGradient>
        <radialGradient id="silkPhoto" cx=".45" cy=".4" r=".7">
          <stop offset="0" stop-color="#d9d9de"/>
          <stop offset=".35" stop-color="#b8245f"/>
          <stop offset="1" stop-color="#7a1546"/>
        </radialGradient>
      </defs>
      <rect width="734" height="520" fill="url(#silverFront)"/>
      <path d="M 296 0 C 222 150, 232 390, 342 520 L 734 520 L 734 0 Z" fill="url(#goldBand)"/>
      <path d="M 314 0 C 244 150, 254 390, 362 520 L 734 520 L 734 0 Z" fill="url(#magentaFront)"/>
      <path d="M 734 330 C 720 430, 650 500, 590 520" fill="none" stroke="#ffffff" stroke-width="3" opacity=".8"/>
      <path d="M 734 360 C 724 440, 680 500, 640 520 L 734 520 Z" fill="url(#goldBand)"/>
      <circle cx="193" cy="231" r="196" fill="var(--gold)" opacity=".85"/>
      <circle cx="193" cy="231" r="176" fill="url(#silkPhoto)" role="img" aria-label="Diamond solitaire engagement ring resting on magenta silk"/>
      <g stroke="#ffffff" stroke-width="1.5">
        <line x1="412" y1="289" x2="545" y2="289"/>
        <line x1="563" y1="289" x2="700" y2="289"/>
      </g>
      <path d="M 554 283 L 560 289 L 554 295 L 548 289 Z" fill="#ffffff"/>
    </svg>

    <div class="txt brand-mark"><div class="dot"></div><div class="name">MARIGOLD JEWELLERY</div></div>
    <div class="txt headline">MARIGOLD<br>JEWELLERY</div>
    <div class="txt tagline-lead">The perfect</div>
    <div class="txt tagline-main">CREATION</div>
    <div class="txt call-label">CALL US TODAY</div>
    <div class="txt call-phone">(02) 6174 3019</div>
  </section>

  <!-- Back -->
  <section class="flyer flyer--back">
    <svg class="art" viewBox="0 0 734 520" xmlns="http://www.w3.org/2000/svg">
      <defs>
        <linearGradient id="magentaBack" x1="0" y1="0" x2="0" y2="1">
          <stop offset="0" stop-color="#b51d52"/>
          <stop offset=".55" stop-color="#c81c5c"/>
          <stop offset="1" stop-color="#6a1848"/>
        </linearGradient>
        <linearGradient id="portraitPhoto" x1="0" y1="0" x2="1" y2="1">
          <stop offset="0" stop-color="#8a5a3a"/>
          <stop offset=".35" stop-color="#e2bba6"/>
          <stop offset=".8" stop-color="#f1d2c4"/>
          <stop offset="1" stop-color="#d9a898"/>
        </linearGradient>
        <linearGradient id="goldSwoosh" x1="0" y1="0" x2="1" y2="0">
          <stop offset="0" stop-color="#b5844a"/>
          <stop offset=".5" stop-color="#e6c48c"/>
          <stop offset="1" stop-color="#c09058"/>
        </linearGradient>
        <radialGradient id="mapTone" cx=".5" cy=".5" r=".6">
          <stop offset="0" stop-color="#f1efe9"/>
          <stop offset="1" stop-color="#d8d6cf"/>
        </radialGradient>
      </defs>
      <rect width="734" height="520" fill="url(#magentaBack)"/>
      <path d="M 0 0 H 300 C 290 180, 280 330, 330 520 H 0 Z" fill="url(#portraitPhoto)" role="img" aria-label="Model with styled hair wearing diamond chandelier earrings"/>
      <path d="M 250 520 C 330 440, 520 410, 734 392" fill="none" stroke="#ffffff" stroke-width="10"/>
      <path d="M 280 520 C 360 450, 540 420, 734 404 V 520 Z" fill="url(#goldSwoosh)"/>
      <g stroke="#ffffff" stroke-width="1.5">
        <line x1="386" y1="159" x2="520" y2="159"/><line x1="540" y1="159" x2="675" y2="159"/>
        <line x1="386" y1="205" x2="520" y2="205"/><line x1="540" y1="205" x2="675" y2="205"/>
        <line x1="386" y1="250" x2="520" y2="250"/><line x1="540" y1="250" x2="675" y2="250"/>
      </g>
      <g fill="#ffffff">
        <path d="M 530 154 L 535 159 L 530 164 L 525 159 Z"/>
        <path d="M 530 200 L 535 205 L 530 210 L 525 205 Z"/>
        <path d="M 530 245 L 535 250 L 530 255 L 525 250 Z"/>
      </g>
      <circle cx="523" cy="391" r="88" fill="var(--gold)"/>
      <circle cx="523" cy="391" r="83" fill="url(#mapTone)" role="img" aria-label="Simplified street map of Griffith showing the store location"/>
    </svg>

    <div class="txt back-title">MARIGOLD JEWELLERY</div>
    <div class="txt service" style="top:120px">specialized in hand made jewellery</div>
    <div class="txt service" style="top:166px">on site jeweller and designer</div>
    <div class="txt service" style="top:212px">repair and restoring</div>
    <div class="txt service" style="top:258px">laser engraving and laser solder</div>
    <div class="txt address">5/41 Marrowind Crescent Griffith ACT 2603</div>
  </section>

</div>
</body>
</html>
```